I need a business card for my original fine art pieces

I would like a business card design including a logo design for a new business in the art world. I am based in the Hunter Valley NSW Australia. I am a contemporary figurative, encaustic and wildlife artist. I would like to be able to upload my email and mobile number to this as well. This design should be one that I can incorporate into banners and flyers etc. Id like to incorporate one of my own images or partial image into the background or somewhere below. My initials are RJ and I would like these used as a logo type. I would like the use of some colour and it to be bright and catchy. The final design should communicate artwork custom made and commissions available.

Overview: Original Fine Artworks for sale, online, art galleries etc, Custom made to order and by commission.

Target market is world wide audience and corporate world

My figurative work is painted using acrylics in a lot of natural ochre colours that reflect the Australian Outback, on canvas, linen, paper or board: My encaustic work is created in a contemporary abstract style using a blow torch and a made with a medium of 100% pure bees wax, Damar resin, mixed media and coloured pigments, applied to Birch board. My wildlife are created using coloured pencil and mixed media on a variety of paper types or board.

```html
<!DOCTYPE html>
<html lang="en">
<head>
<meta charset="utf-8">
<title>Rhea Jansen – Business Card</title>
<link href="https://fonts.googleapis.com/css2?family=Cinzel:wght@500&family=Montserrat:wght@500&family=Cabin:wght@400;500&display=swap" rel="stylesheet">
<style>
  :root {
    --accent: #ef4a1f;
    --ink: #111111;
    --paper: #ffffff;
    --paper-soft: #f1f3f2;
    --stage: #e4e4e4;
    --muted: #444444;
  }
  * { box-sizing: border-box; margin: 0; padding: 0; }
  html, body { width: 1200px; height: 900px; overflow: hidden; }
  body { background: var(--stage); position: relative; font-family: 'Cabin', sans-serif; }

  .card {
    position: absolute; width: 640px; height: 370px;
    border-radius: 22px; overflow: hidden; background: var(--paper);
    box-shadow: 0 10px 30px rgba(0,0,0,.18);
  }
  .card--front { left: 80px; top: 50px; background: var(--paper-soft); }
  .card--back { left: 480px; top: 470px; }

  .artwork-panel {
    position: absolute; left: 0; top: 0; width: 300px; height: 100%;
    background: linear-gradient(90deg, #2a2a2a 0%, #5a5a5a 35%, #d8d8d8 75%, var(--paper-soft) 100%);
  }

  .monogram {
    position: absolute; width: 120px; height: 120px; border-radius: 50%;
    border: 4px solid var(--accent); background: var(--paper);
    display: flex; align-items: center; justify-content: center;
    font-family: 'Cinzel', serif; font-weight: 500; font-size: 52px; color: var(--accent);
  }
  .card--front .monogram { left: 405px; top: 30px; }

  .wordmark {
    position: absolute; font-family: 'Cinzel', serif; font-weight: 500;
    color: var(--accent); font-size: 40px; line-height: 1; white-space: nowrap;
  }
  .tagline {
    position: absolute; font-family: 'Montserrat', sans-serif; font-weight: 500;
    color: var(--ink); font-size: 15px; letter-spacing: 2.6px; white-space: nowrap;
  }
  .card--front .wordmark { left: 342px; top: 170px; }
  .card--front .tagline { left: 344px; top: 214px; }

  .website { position: absolute; font-size: 17px; color: var(--ink); }
  .website span { color: var(--accent); }
  .card--front .website { right: 40px; top: 290px; }

  .swoosh { position: absolute; inset: 0; }

  .card--back .wordmark { left: 34px; top: 100px; font-size: 38px; }
  .card--back .tagline { left: 36px; top: 142px; font-size: 14px; }
  .person { position: absolute; left: 0; width: 390px; top: 180px; text-align: center; }
  .person__name { font-family: 'Cinzel', serif; font-weight: 500; color: var(--accent); font-size: 26px; }
  .person__role { font-size: 15px; color: var(--muted); margin-top: 2px; }
  .offer { position: absolute; left: 10px; width: 370px; top: 248px; text-align: center; font-size: 14px; line-height: 1.35; color: var(--ink); font-weight: 500; }

  .card--back .monogram { left: 395px; top: 22px; width: 140px; height: 140px; font-size: 60px; }

  .contact {
    position: absolute; right: 18px; top: 180px; list-style: none;
    color: var(--paper); font-size: 16px; text-align: right; line-height: 1.55;
  }
  .contact li { display: flex; justify-content: flex-end; align-items: center; gap: 10px; }
  .contact .icon { width: 14px; height: 14px; flex: none; }
  .contact .spacer { width: 14px; flex: none; }
  .contact .hl { color: var(--accent); }
</style>
</head>
<body>

<section class="card card--front">
  <div class="artwork-panel" role="img" aria-label="Figurative artwork by the artist, in black, white and red tones"></div>
  <div class="monogram">RJ</div>
  <div class="wordmark">RHEA JANSEN</div>
  <div class="tagline">ORIGINAL FINE ARTWORKS</div>
  <div class="website">www.<span>rheajansen</span>.com</div>
</section>

<section class="card card--back">
  <svg class="swoosh" viewBox="0 0 640 370" preserveAspectRatio="none" aria-hidden="true">
    <path d="M500 0 H640 V370 H220 C330 360 420 310 450 230 C475 160 485 80 500 0 Z" fill="var(--ink)"/>
    <path d="M0 340 C120 360 260 360 340 322 C410 288 440 232 452 150" fill="none" stroke="var(--ink)" stroke-width="10"/>
    <path d="M0 358 C130 378 280 372 362 334 C432 298 460 242 472 162" fill="none" stroke="var(--accent)" stroke-width="8"/>
    <path d="M520 60 L640 18 V36 L525 76 Z" fill="var(--accent)"/>
  </svg>

  <div class="wordmark">RHEA JANSEN</div>
  <div class="tagline">ORIGINAL FINE ARTWORKS</div>
  <div class="person">
    <div class="person__name">Rhea Jansen</div>
    <div class="person__role">Director</div>
  </div>
  <p class="offer">Original Fine Artworks for sale<br>online, art galleries etc<br>Custom made to order and by commission.</p>

  <div class="monogram">RJ</div>

  <ul class="contact">
    <li><span>Perth Australia</span> <i class="spacer"></i></li>
    <li><span>ABN 12 345 678 901</span> <i class="spacer"></i></li>
    <li><span>+61 400 218 734</span>
      <svg class="icon" viewBox="0 0 14 14"><rect x="3.5" y="1" width="7" height="12" rx="1.5" fill="none" stroke="var(--accent)" stroke-width="1.5"/><circle cx="7" cy="10.5" r=".9" fill="var(--accent)"/></svg></li>
    <li><span>rhea@jansen.com</span>
      <svg class="icon" viewBox="0 0 14 14"><rect x="1" y="3" width="12" height="8" rx="1" fill="none" stroke="var(--accent)" stroke-width="1.5"/><path d="M1.5 3.5 L7 8 L12.5 3.5" fill="none" stroke="var(--accent)" stroke-width="1.3"/></svg></li>
    <li><span>www.<span class="hl">rheajansen</span>.com</span>
      <svg class="icon" viewBox="0 0 14 14"><circle cx="7" cy="7" r="5.8" fill="none" stroke="var(--accent)" stroke-width="1.4"/><path d="M1.5 7 H12.5 M7 1.2 C4 4.5 4 9.5 7 12.8 M7 1.2 C10 4.5 10 9.5 7 12.8" fill="none" stroke="var(--accent)" stroke-width="1.1"/></svg></li>
  </ul>
</section>

</body>
</html>
```